business card deign

Logo needs the following on it.
1. attached logo
2. Tagline - "If it keeps the ice frosty or the night rolling...we bring it!"
3. Name- Dalton Pikes, Founder and CPO
4. Address - 412 E. Carver Avenue, Ste 2207, Tampa, FL. 33917
5. Phone - 555.318.4726

```html
<!DOCTYPE html>
<html lang="en">
<head>
<meta charset="utf-8">
<title>Hopwell Business Card</title>
<link rel="stylesheet" href="https://fonts.googleapis.com/css2?family=Arimo:wght@400;700&display=swap">
<style>
  :root {
    --stage: #d9d9d9;
    --card-white: #ffffff;
    --card-white-edge: #ececec;
    --card-black: #0b0b0b;
    --ink: #111111;
    --text-light: #f2f2f2;
    --gold-light: #f3e27a;
    --gold-deep: #c98a2c;
    --rule: #6b5426;
  }
  * { box-sizing: border-box; margin: 0; padding: 0; }
  html, body {
    width: 1200px;
    height: 900px;
    overflow: hidden;
    background: var(--stage);
    font-family: "Arimo", Arial, sans-serif;
  }
  .stage {
    width: 1200px;
    height: 900px;
    display: flex;
    flex-direction: column;
    align-items: center;
    justify-content: center;
    gap: 40px;
  }
  .card {
    width: 640px;
    height: 366px;
    border-radius: 30px;
    position: relative;
    overflow: hidden;
    box-shadow: 0 10px 24px rgba(0,0,0,0.25);
  }
  .card-front {
    background: linear-gradient(160deg, var(--card-white) 40%, var(--card-white-edge));
    display: flex;
    align-items: center;
    justify-content: center;
  }
  .brand-front {
    display: flex;
    align-items: center;
    gap: 18px;
  }
  .brand-dot {
    width: 22px;
    height: 22px;
    border-radius: 50%;
    background: var(--ink);
  }
  .brand-name-front {
    font-weight: 700;
    font-size: 40px;
    letter-spacing: 14px;
    color: var(--ink);
  }
  .card-back {
    background: var(--card-black);
    color: var(--text-light);
    text-align: center;
    padding-top: 52px;
  }
  .brand-back {
    display: flex;
    align-items: center;
    justify-content: center;
    gap: 14px;
    height: 96px;
  }
  .brand-dot-light {
    width: 18px;
    height: 18px;
    border-radius: 50%;
    background: var(--text-light);
  }
  .brand-name-back {
    font-weight: 700;
    font-size: 30px;
    letter-spacing: 10px;
    color: var(--text-light);
  }
  .holder {
    margin-top: 20px;
    font-size: 19px;
  }
  .holder-name { font-weight: 700; text-transform: uppercase; }
  .holder-sep { font-weight: 700; margin: 0 4px; }
  .rule {
    width: 420px;
    height: 1px;
    margin: 10px auto;
    background: linear-gradient(90deg, transparent, var(--rule), transparent);
  }
  .contact {
    font-size: 15px;
    display: flex;
    align-items: center;
    justify-content: center;
    gap: 7px;
    line-height: 1.5;
  }
  .contact svg { width: 14px; height: 14px; fill: var(--text-light); }
  .tagline {
    margin-top: 14px;
    font-weight: 700;
    font-size: 19px;
    white-space: nowrap;
    background: linear-gradient(90deg, var(--gold-light), var(--gold-deep), var(--gold-light));
    -webkit-background-clip: text;
    background-clip: text;
    color: transparent;
  }
</style>
</head>
<body>
<main class="stage">
  <section class="card card-front">
    <div class="brand-front">
      <span class="brand-dot"></span>
      <span class="brand-name-front">HOPWELL</span>
    </div>
  </section>

  <section class="card card-back">
    <div class="brand-back">
      <span class="brand-dot-light"></span>
      <span class="brand-name-back">HOPWELL</span>
    </div>
    <p class="holder"><span class="holder-name">Dalton Pikes</span><span class="holder-sep">|</span>Founder and CPO</p>
    <div class="rule"></div>
    <p class="contact">
      <svg viewBox="0 0 24 24" aria-hidden="true"><path d="M6.6 10.8a15.1 15.1 0 0 0 6.6 6.6l2.2-2.2a1 1 0 0 1 1-.25 11.4 11.4 0 0 0 3.6.57 1 1 0 0 1 1 1V20a1 1 0 0 1-1 1A17 17 0 0 1 3 4a1 1 0 0 1 1-1h3.5a1 1 0 0 1 1 1c0 1.250.2 2.45.57 3.6a1 1 0 0 1-.25 1z"/></svg>
      555.318.4726
    </p>
    <p class="contact">
      <svg viewBox="0 0 24 24" aria-hidden="true"><path d="M12 2a7 7 0 0 0-7 7c0 5.25 7 13 7 13s7-7.75 7-13a7 7 0 0 0-7-7zm0 9.5A2.5 2.5 0 1 1 12 6.5a2.5 2.5 0 0 1 0 5z"/></svg>
      412 E. Carver Avenue, Ste 2207, Tampa, FL. 33917
    </p>
    <div class="rule"></div>
    <p class="tagline">If it keeps the ice frosty or the night rolling...we bring it!</p>
  </section>
</main>
</body>
</html>
```